Brightfen Business Card Redesign & Logo Update

We need to update our business cards to something more modern and fresh. Brightfen can provide the current color schemes and old design examples, but welcome creativity in helping us with this redesign. PLEASE NOTE that we no longer utilize the "tree" and/or "leaf" imagery in our branding. If able would apprecaite an update on the quality of our "words only" logo in Ai. / PNG formats too.

Target Market(s)

Investors, landowners, corporate partners, contractors

Industry/Entity Type

Environmental Restoration & Conservation

Contact Information for Business Card

Logo, persons name, title, mailing address, phone and email, website url

Font styles to use
Other font styles liked:
• Merriweather

Requirements
Nice to have
• Logo, persons name, title, mailing address, phone and email, website url, but open to ideams
Should not have
• No all back backgrounds

```html
<!DOCTYPE html>
<html lang="en">
<head>
<meta charset="utf-8">
<title>Brightfen Business Card</title>
<link href="https://fonts.googleapis.com/css2?family=Open+Sans:wght@400;600;800&family=Montserrat:wght@700&display=swap" rel="stylesheet">
<style>
  :root {
    --page: #e9eae8;
    --card: #232226;
    --green: #148040;
    --orange: #ef7f22;
    --white: #ffffff;
  }
  * { margin: 0; padding: 0; box-sizing: border-box; }
  html, body { width: 1200px; height: 780px; overflow: hidden; background: var(--page); }
  .sheet {
    width: 1200px; height: 780px;
    display: flex; align-items: center; justify-content: center; gap: 40px;
  }
  .card {
    position: relative;
    width: 560px; height: 320px;
    background: var(--card);
    border-radius: 18px;
    overflow: hidden;
    font-family: "Open Sans", sans-serif;
    color: var(--white);
  }
  .swoop { position: absolute; inset: 0; width: 100%; height: 100%; }
  .wordmark {
    position: absolute;
    font-family: "Open Sans", sans-serif;
    font-weight: 800;
    color: var(--orange);
    text-transform: uppercase;
    letter-spacing: 1px;
    line-height: 1;
  }
  .card-front .wordmark {
    left: 0; right: 0; top: 92px;
    text-align: center; font-size: 66px;
  }

  .card-back .wordmark { left: 34px; top: 48px; font-size: 38px; }
  .accent-bar {
    position: absolute; right: 0; top: 20px;
    width: 18px; height: 46px; background: var(--green);
  }
  .person { position: absolute; right: 36px; top: 26px; text-align: right; }
  .person-name { font-family: "Montserrat", sans-serif; font-weight: 700; font-size: 22px; letter-spacing: 1px; }
  .person-title { font-size: 12px; margin-top: 2px; letter-spacing: 0.5px; }
  .contacts {
    position: absolute; right: 26px; top: 176px;
    list-style: none; text-align: right;
    font-size: 14px; line-height: 25px;
  }
  .contacts li { display: flex; align-items: center; justify-content: flex-end; gap: 8px; }
  .contacts svg { width: 14px; height: 14px; fill: var(--white); flex: none; }
</style>
</head>
<body>
<main class="sheet">
  <section class="card card-front">
    <svg class="swoop" viewBox="0 0 560 320" aria-hidden="true">
      <path d="M0 262 C160 262 300 226 400 236 C470 243 520 256 560 250 L560 320 L0 320 Z" fill="var(--green)"/>
      <path d="M0 250 C160 250 300 214 400 224 C470 231 520 244 560 238" fill="none" stroke="var(--orange)" stroke-width="5"/>
    </svg>
    <div class="wordmark">Brightfen</div>
  </section>

  <section class="card card-back">
    <svg class="swoop" viewBox="0 0 560 320" aria-hidden="true">
      <path d="M0 302 C150 302 232 252 300 180 C350 130 400 120 560 118 L560 320 L0 320 Z" fill="var(--green)"/>
      <path d="M0 290 C148 290 222 242 290 170 C336 122 380 110 470 106" fill="none" stroke="var(--orange)" stroke-width="5"/>
    </svg>
    <div class="wordmark">Brightfen</div>
    <div class="accent-bar"></div>
    <div class="person">
      <div class="person-name">Lena Marsh</div>
      <div class="person-title">Managing Director</div>
    </div>
    <ul class="contacts">
      <li>(555) 214-0387
        <svg viewBox="0 0 24 24"><path d="M6.6 10.8a15 15 0 0 0 6.6 6.6l2.2-2.2c.3-.3.7-.4 1-.2 1.1.4 2.3.6 3.6.6.6 0 1 .4 1 1V20c0 .6-.4 1-1 1A17 17 0 0 1 3 4c0-.6.4-1 1-1h3.5c.6 0 1 .4 1 1 0 1.3.2 2.5.6 3.6.1.3 0 .7-.2 1z"/></svg>
      </li>
      <li>info@brightfen.com
        <svg viewBox="0 0 24 24"><path d="M2 5h20v14H2z M4 7v.5l8 5 8-5V7l-8 5z" fill-rule="evenodd"/></svg>
      </li>
      <li>www.brightfen.com
        <svg viewBox="0 0 24 24"><circle cx="12" cy="12" r="10"/></svg>
      </li>
      <li>1420 Cedar Row, Austin, TX 78701
        <svg viewBox="0 0 24 24"><path d="M12 2a7 7 0 0 0-7 7c0 5 7 13 7 13s7-8 7-13a7 7 0 0 0-7-7zm0 9.5a2.5 2.5 0 1 1 0-5 2.5 2.5 0 0 1 0 5z"/></svg>
      </li>
    </ul>
  </section>
</main>
</body>
</html>
```